Kitchen and custom cabinetry company looking for business card design

We make: * Custom Kitchens, contemporary and traditional kitchens, Vanities, Libraries, Custom Entry Doors, Custom Wine Cellars and Custom Design Furniture. Phone number 555-284-7716. Address: Westhampton NY. Email: KAVRO@mailbox.example Portfolio at: KAVROcabinetry.example I would like moderns fonts and not heavy lines. double side but maybe will use clear plastic. I attached the logo.

Industry/Entity Type

Business

```html
<!DOCTYPE html>
<html lang="en">
<head>
<meta charset="utf-8">
<title>KAVRO Cabinetry Inc. – Business Card</title>
<link rel="stylesheet" href="https://fonts.googleapis.com/css2?family=Quicksand:wght@300;400;500&display=swap">
<style>
  :root {
    --orange: #f15a29;
    --orange-soft: #f5845f;
    --grey: #808080;
    --grey-soft: #b8b8b8;
    --logo-grey: #7a7a7a;
    --paper: #ffffff;
    --backdrop: #ddd6cc;
    --card-text: #ffffff;
  }
  * { box-sizing: border-box; margin: 0; padding: 0; }
  html, body { width: 1200px; height: 970px; overflow: hidden; }
  body {
    position: relative;
    background: var(--backdrop);
    font-family: "Quicksand", sans-serif;
  }
  .card-side { position: absolute; width: 409px; }
  .card-side.left { left: 125px; }
  .card-side.right { left: 608px; }

  .front {
    position: absolute; top: 128px; left: 0; width: 409px; height: 298px;
    border-radius: 23px 23px 0 0; overflow: hidden; background: var(--paper);
  }
  .front-band { height: 30px; }
  .left .front-band { background: var(--orange); }
  .right .front-band { background: var(--grey); }

  .wordmark {
    position: absolute; top: 30px; left: 0; right: 0; bottom: 0;
    display: flex; flex-direction: column; align-items: center; justify-content: center;
    color: var(--logo-grey); font-weight: 500; text-align: center;
  }
  .wordmark-name { font-size: 66px; letter-spacing: 4px; line-height: 1; }
  .wordmark-sub { font-size: 19px; letter-spacing: 7px; margin-top: 8px; }

  .divider-strip { position: absolute; top: 452px; left: 0; width: 409px; height: 48px; }
  .left .divider-strip { background: var(--orange-soft); }
  .right .divider-strip { background: var(--grey-soft); }

  .back {
    position: absolute; top: 522px; left: 0; width: 409px; height: 322px;
    border-radius: 0 0 25px 25px; color: var(--card-text); text-align: center;
    font-weight: 400;
  }
  .left .back { background: var(--orange); }
  .right .back { background: var(--grey); }

  .holder-name { position: absolute; top: 50px; width: 100%; font-size: 25px; letter-spacing: 1px; }
  .holder-role { position: absolute; top: 80px; width: 100%; font-size: 16px; font-weight: 300; letter-spacing: 1px; }
  .contact { position: absolute; top: 127px; width: 100%; font-size: 17px; line-height: 21px; letter-spacing: 0.5px; }
  .address { position: absolute; top: 231px; width: 100%; font-size: 18px; line-height: 21px; letter-spacing: 0.5px; }

  .services { position: absolute; top: 94px; width: 100%; list-style: none; }
  .services li { font-size: 19.5px; line-height: 28.4px; letter-spacing: 1px; text-transform: uppercase; }
</style>
</head>
<body>
  <section class="card-side left">
    <div class="front">
      <div class="front-band"></div>
      <div class="wordmark">
        <span class="wordmark-name">KAVRO</span>
        <span class="wordmark-sub">CABINETRY INC.</span>
      </div>
    </div>
    <div class="divider-strip"></div>
    <div class="back">
      <p class="holder-name">Marco Delgado</p>
      <p class="holder-role">Owner</p>
      <p class="contact">555&nbsp;&nbsp;284&nbsp;&nbsp;7716<br>kavro@mailbox.example<br>www.kavrocabinetry.example</p>
      <p class="address">2210 Harbor Mill rd,<br>Eastbrook, NY, 10021</p>
    </div>
  </section>

  <section class="card-side right">
    <div class="front">
      <div class="front-band"></div>
      <div class="wordmark">
        <span class="wordmark-name">KAVRO</span>
        <span class="wordmark-sub">CABINETRY INC.</span>
      </div>
    </div>
    <div class="divider-strip"></div>
    <div class="back">
      <ul class="services">
        <li>Contemporay Kitchens</li>
        <li>Traditional Kitchens</li>
        <li>Vanities</li>
        <li>Libraries</li>
        <li>Custom Wine Cellars</li>
        <li>Custom Design Furniture</li>
      </ul>
    </div>
  </section>
</body>
</html>
```